Moon Tot needs ecommerce website design help

We need someone to set up a fully functional website for us. We sell baby bibs, I attached them along with our company logo (MTG: moon tot goods). The bibs are made of 100% silicon, they are safe, light weight, soft, smooth, flexible, dishwasher safe and has funny faces.

Business name: Moon Tot Goods
Elm Hollow, NY 00000
email: MoonTotGoods@mailbox-example.com
tel.: (555) 014-TOTS
website: MoonTotGoods-example.com

Target Market(s)

18-40

Industry/Entity Type

Baby

Coding

Coded - Design and coding required

Number of Pages Required

5+ page

Requirements
Must have
• 1. Pages: Why buy from us, Contact Us, Home page, Products Page, Blog
• 2. Use the colors from our logo for the web design.
• 3. Need a link that will connect visitors to our facebook, instagram, Pinterest and Tumblr account. Would like links on,the top left side of the page
Nice to have
• My Cart page
• 1. On contact us page, we want to include some type of template for the customer to complete. (Ex: name, email address, contact number, optional home address, comments)
• 2. When clients visit our website, we want a capture/pop up for the customer to subscribe to our email list to receive discounts. (Ex. Want 10% off your next order ? Suscribe to our mailing list below and get a 10% off code to use at check out. If they don't want to subscribe, they have the option to select "No Thank You, I want to pay full price).
• 3. On home page have subscribe to our email list.

```html
<!DOCTYPE html>
<html lang="en">
<head>
<meta charset="utf-8">
<title>Moon Tot Goods – Home</title>
<link href="https://fonts.googleapis.com/css2?family=Open+Sans:ital,wght@0,300;0,400;0,600;0,700;1,400&display=swap" rel="stylesheet">
<style>
:root{
  --green:#a3c521;
  --pink:#e23a5c;
  --orange:#f2a52b;
  --red:#d0334f;
  --band:#c9304c;
  --ink:#333;
  --muted:#8a8a8a;
  --light:#f3f3f3;
  --footer:#1e1e1e;
  --olive:#9fae2a;
  --white:#fff;
}
*{box-sizing:border-box;margin:0;padding:0}
html,body{width:782px;height:1200px;overflow:hidden}
body{position:relative;background:var(--white);font-family:"Open Sans",Arial,sans-serif;color:var(--ink)}
.abs{position:absolute}
a{color:inherit;text-decoration:none}

.topbar{left:0;top:0;width:782px;height:29px;background:#fafafa;border-bottom:1px solid #eee;font-size:6.5px;color:var(--muted)}
.topbar span{position:absolute;top:9px;white-space:nowrap}
.topbar .cart{color:var(--red)}
.cart-icon{position:absolute;left:683px;top:7px;width:12px;height:11px;background:var(--red);border-radius:0 0 3px 3px}

.brand{left:86px;top:40px;display:flex;align-items:center;gap:8px}
.brand-dot{width:40px;height:40px;border-radius:50%;background:var(--orange)}
.brand-name{font-size:20px;font-weight:400;color:var(--ink)}
.search{left:570px;top:46px;width:124px;height:22px;border:1px solid #ddd;font-size:7px;color:#999;padding:6px 10px}
.search svg{position:absolute;right:6px;top:5px}
.nav{top:88px;font-size:8px;color:#444;white-space:nowrap}

.hero{left:0;top:117px;width:782px;height:259px;background:var(--light)}
.hero-photo{left:344px;top:117px;width:438px;height:259px;background:linear-gradient(110deg,#f3f1ee 0%,#e9d7c8 35%,#c98a6a 60%,#b03a6f 80%,#efe9e5 100%)}
.hero-title{left:85px;top:182px;font-size:28px;line-height:30px;color:#777;font-weight:300;white-space:nowrap}
.hero-text{left:86px;top:248px;font-size:7px;line-height:12px;color:#666;width:250px}
.btn{background:var(--red);color:#fff;font-size:9px;text-align:center;white-space:nowrap}
.hero-btn{left:86px;top:277px;width:68px;height:26px;line-height:26px}
.arrow{top:238px}

.welcome{left:0;top:376px;width:782px;height:130px;background:var(--band);color:#fff;text-align:center}
.welcome h2{font-weight:400;font-size:21px;margin-top:20px}
.welcome p{font-size:6.8px;line-height:13.5px;width:610px;margin:9px auto 0;opacity:.85}

.products-title{left:0;width:782px;top:538px;text-align:center;font-size:21px;color:var(--olive);font-weight:400}
.pager{top:547px;width:15px;height:13px;border:1px solid #999}
.product{top:584px;width:180px;text-align:center}
.product .pic{width:130px;height:168px;margin:0 auto;border-radius:30px 30px 60px 60px}
.product h3{font-weight:400;font-size:12.5px;margin-top:14px;color:#333;white-space:nowrap}
.product .price{font-size:9.5px;color:var(--olive);margin-top:6px}
.product .add{width:22px;height:22px;border-radius:50%;background:var(--red);margin:8px auto 0;display:flex;align-items:center;justify-content:center}
.divider{top:584px;width:1px;height:260px;background:#eee}

.promo{top:869px;width:195px;height:129px;background:#f5f5f5;overflow:hidden}
.promo .img{position:absolute;left:0;top:0;height:129px}
.promo h4{position:absolute;right:12px;text-align:right;font-weight:700;color:var(--orange);white-space:nowrap}
.promo .small{position:absolute;right:12px;text-align:right;font-size:5px;line-height:9px;color:#888;white-space:nowrap}
.promo .btn{position:absolute;right:8px;height:20px;line-height:20px;font-size:7.5px;padding:0 10px}

.footer{left:0;top:1048px;width:782px;height:152px;background:var(--footer);color:#888}
.footer h5{position:absolute;top:26px;font-weight:400;font-size:8px;color:#bbb;white-space:nowrap}
.footer ul{position:absolute;top:42px;list-style:none;font-size:6.5px;line-height:12.5px;white-space:nowrap}
.footer li::before{content:"›  ";color:var(--red)}
.f-input{position:absolute;left:401px;top:40px;width:142px;height:24px;background:#fff;font-size:6.5px;color:#999;padding:8px 9px}
.f-go{position:absolute;left:526px;top:40px;width:17px;height:24px;background:var(--orange)}
.social{position:absolute;top:49px;width:17px;height:17px;border:1px solid #aaa;border-radius:50%}
.card{position:absolute;top:82px;width:16px;height:9px;border-radius:1px}
.copy{position:absolute;left:0;width:782px;top:130px;text-align:center;font-size:6.5px;color:#777}

.overlay{left:0;top:0;width:782px;height:1200px;background:rgba(0,0,0,.58)}
.modal{left:260px;top:70px;width:261px;height:260px;background:#fff;text-align:center}
.modal .m-brand{margin-top:28px;display:flex;align-items:center;justify-content:center;gap:8px}
.modal .m-brand .brand-dot{width:34px;height:34px}
.modal .m-brand span{font-size:19px;color:var(--ink)}
.modal h2{font-size:14px;font-weight:700;color:var(--pink);margin-top:21px;letter-spacing:.2px;white-space:nowrap}
.modal .sub{font-size:12px;margin-top:2px;color:#222}
.modal .offer{font-size:7.5px;color:#e08b1d;margin-top:11px}
.modal .body{font-size:7.2px;line-height:11px;color:#222;margin:5px auto 0;width:215px}
.m-form{position:absolute;left:23px;top:188px;width:215px;height:29px;display:flex}
.m-form .field{flex:1;border:1px solid #ddd;border-right:none;font-size:6.5px;color:#666;text-align:left;padding:10px 12px}
.m-form .go{width:69px;background:var(--green);color:#fff;font-size:8.5px;font-weight:600;line-height:29px}
.modal .decline{position:absolute;left:0;width:261px;top:231px;font-size:7px;font-style:italic;color:#555;text-decoration:underline}
</style>
</head>
<body>

<div class="topbar abs">
  <span style="left:86px">● Elm Hollow, NY 00000</span>
  <span style="left:172px">|&nbsp; ☎ Tel : (555) 014-TOTS</span>
  <span style="left:252px">|&nbsp; ✉ Email : MoonTotGoods@mailbox-example.com</span>
  <span style="left:452px">My Account</span>
  <span style="left:506px">|&nbsp; My Wishlist</span>
  <span style="left:562px">|&nbsp; Checkout</span>
  <span class="cart" style="left:621px">My Cart : 0 Items</span>
  <div class="cart-icon"></div>
</div>

<header>
  <div class="brand abs"><div class="brand-dot"></div><span class="brand-name">Moon Tot Goods</span></div>
  <div class="search abs">Search
    <svg width="10" height="10" viewBox="0 0 10 10"><circle cx="4" cy="4" r="3" fill="none" stroke="#555" stroke-width="1.3"/><line x1="6.2" y1="6.2" x2="9" y2="9" stroke="#555" stroke-width="1.4"/></svg>
  </div>
  <nav>
    <a class="nav abs" style="left:400px">Home</a>
    <a class="nav abs" style="left:450px">Products</a>
    <a class="nav abs" style="left:533px">Why buy from us</a>
    <a class="nav abs" style="left:618px">Blog</a>
    <a class="nav abs" style="left:656px">Contact us</a>
  </nav>
</header>

<section>
  <div class="hero abs"></div>
  <div class="hero-photo abs" role="img" aria-label="Photo of a toddler eating while wearing a silicone bib"></div>
  <h1 class="hero-title abs">Phasellus nisl eget<br>condimentum vel</h1>
  <p class="hero-text abs">Aenean sed quam non sapien faucibus consequat vel orci. Praesent quis risus mi.</p>
  <a class="btn hero-btn abs">Buy Now</a>
  <svg class="arrow abs" style="left:16px" width="10" height="16" viewBox="0 0 10 16"><polyline points="8,1 2,8 8,15" fill="none" stroke="#888" stroke-width="1.5"/></svg>
  <svg class="arrow abs" style="left:756px" width="10" height="16" viewBox="0 0 10 16"><polyline points="2,1 8,8 2,15" fill="none" stroke="#888" stroke-width="1.5"/></svg>
</section>

<section class="welcome abs">
  <h2>Welcome to Moon Tot Goods</h2>
  <p>Fusce sollicitudin lorem et luctus volutpat. Proin placerat dapibus gravida. In tristique tristique nulla eget hendrerit. Maecenas vel tortor accumsan quam varius imperdiet vel eget elit. Aenean facilisis tincidunt lectus, id dictum nisl luctus eget. Vivamus efficitur ex condimentum, malesuada eros eget, feugiat nibh. Sed tellus ex, imperdiet eget gravida sit amet, volutpat eget turpis. In nec ultricies est. Etiam mattis augue vehicula odio posuere, sit amet tempus lectus luctus. Nulla facilisi. Etiam vel massa elementum, bibendum tellus venenatis, feugiat massa. Curabitur venenatis lacinia ornare. Cras sollicitudin cursus dui eu placerat.</p>
</section>

<section>
  <h2 class="products-title abs">Our Products</h2>
  <svg class="pager abs" style="left:285px" viewBox="0 0 15 13"><polyline points="9,3 6,6.5 9,10" fill="none" stroke="#888"/></svg>
  <svg class="pager abs" style="left:482px" viewBox="0 0 15 13"><polyline points="6,3 9,6.5 6,10" fill="none" stroke="#888"/></svg>

  <div class="product abs" style="left:82px">
    <div class="pic" style="background:linear-gradient(#f6b41e,#ef9c16)" role="img" aria-label="Orange tiger-face silicone bib"></div>
    <h3>Orange Tiger Bib</h3><div class="price">$00.00</div>
    <div class="add"><svg width="9" height="9" viewBox="0 0 9 9"><rect x="1" y="3" width="7" height="5.5" fill="#fff"/><path d="M3 3V2a1.5 1.5 0 0 1 3 0v1" fill="none" stroke="#fff"/></svg></div>
  </div>
  <div class="divider abs" style="left:281px"></div>
  <div class="product abs" style="left:300px">
    <div class="pic" style="background:linear-gradient(#3b9fe0,#1f78c8)" role="img" aria-label="Blue bull-face silicone bib"></div>
    <h3>Blue Bull Bib</h3><div class="price">$00.00</div>
    <div class="add"><svg width="9" height="9" viewBox="0 0 9 9"><rect x="1" y="3" width="7" height="5.5" fill="#fff"/><path d="M3 3V2a1.5 1.5 0 0 1 3 0v1" fill="none" stroke="#fff"/></svg></div>
  </div>
  <div class="divider abs" style="left:500px"></div>
  <div class="product abs" style="left:520px">
    <div class="pic" style="background:linear-gradient(#8fc63a,#5fa12c)" role="img" aria-label="Green frog-face silicone bib"></div>
    <h3>Green Frog Bib</h3><div class="price">$00.00</div>
    <div class="add"><svg width="9" height="9" viewBox="0 0 9 9"><rect x="1" y="3" width="7" height="5.5" fill="#fff"/><path d="M3 3V2a1.5 1.5 0 0 1 3 0v1" fill="none" stroke="#fff"/></svg></div>
  </div>
</section>

<section>
  <div class="promo abs" style="left:86px">
    <div class="img" style="width:100px;background:linear-gradient(#5db3ea,#2a7fcc)" role="img" aria-label="Blue silicone bib"></div>
    <h4 style="top:10px;font-size:17px;line-height:21px">Why buy<br>from us?</h4>
    <p class="small" style="top:60px;font-size:6px;line-height:12.5px">100% Silicon<br>They are Safe<br>Light Weight</p>
    <a class="btn" style="top:101px">Buy Now</a>
  </div>
  <div class="promo abs" style="left:294px">
    <div class="img" style="width:90px;background:linear-gradient(#f1ede6,#e4cdb6)" role="img" aria-label="Photo of a baby eating in a bib"></div>
    <h4 style="top:10px;font-size:17px;color:var(--olive)">Blog</h4>
    <p class="small" style="top:36px;font-size:7px;line-height:11px;color:#666">Etiam vel massa elementum,<br>bibendum tellus</p>
    <p class="small" style="top:61px">Quisque aliquet ut nec vel vehicula.<br>Cras pulvinar. Pellentesque convallis<br>molestie enim sit amet efficitur.</p>
    <a class="btn" style="top:98px;background:#666;right:13px">Read more</a>
  </div>
  <div class="promo abs" style="left:500px">
    <div class="img" style="width:110px;background:linear-gradient(#e8ea3a,#cdd418)" role="img" aria-label="Yellow frog-face silicone bib"></div>
    <h4 style="top:16px;font-size:15px;color:#555;font-weight:600">Special Offer</h4>
    <p class="small" style="top:37px;font-size:10px;line-height:13px;color:#666">32% Offer</p>
    <p class="small" style="top:55px">Quisque aliquet ut nec est<br>vestibulum pulvinar. Pellen<br>tesque convallis</p>
    <a class="btn" style="top:91px;right:15px">Buy Now</a>
  </div>
</section>

<footer class="footer abs">
  <h5 style="left:87px">Links</h5>
  <ul style="left:87px"><li>Home</li><li>Products</li><li>Why buy from us</li><li>Blog</li><li>Contact us</li></ul>
  <h5 style="left:214px">Contact Us</h5>
  <ul style="left:214px;line-height:14.5px"><li>Elm Hollow, NY 00000</li><li>Tel : (555) 014-TOTS</li><li>Email : MoonTotGoods@mailbox-example.com</li></ul>
  <h5 style="left:400px">Newsletter Subscribe</h5>
  <div class="f-input">Email Address</div><div class="f-go"></div>
  <h5 style="left:614px">Connect with us</h5>
  <a class="social" style="left:614px" aria-label="Social network 1"></a>
  <a class="social" style="left:635px" aria-label="Social network 2"></a>
  <a class="social" style="left:656px" aria-label="Social network 3"></a>
  <a class="social" style="left:677px" aria-label="Social network 4"></a>
  <span class="card" style="left:615px;background:#e3a13a"></span>
  <span class="card" style="left:634px;background:#3f6fb8"></span>
  <span class="card" style="left:653px;background:#d8a22c"></span>
  <span class="card" style="left:672px;background:#5a8fd0"></span>
  <p class="copy">Copyright © 2016 Moon Tot Goods. All rights reserved.</p>
</footer>

<div class="overlay abs"></div>
<div class="modal abs" role="dialog" aria-label="Subscribe to our email list">
  <div class="m-brand"><div class="brand-dot"></div><span>Moon Tot Goods</span></div>
  <h2>SUBSCRIBE TO OUR EMAIL LIST</h2>
  <p class="sub">to receive discounts</p>
  <p class="offer">Want 10% off your next order?</p>
  <p class="body">Suscribe to our mailing list below and get a 10% off code to use at checkout</p>
  <div class="m-form"><div class="field">Email Address</div><div class="go">SUBSCRIBE</div></div>
  <a class="decline">No Thank You, I want to pay full price</a>
</div>

</body>
</html>
```